Brivolt Technologies business card design

We need a business card designed with our new logo. it would be great if the card could communicate it is a technology based company.

Target Market(s)

system integrators

Industry/Entity Type

technology, IOT

Contact Information for Business Card

Name, designation, Address, telephone number, email address

Requirements
Must have
• logo and company name
Nice to have
• something to do with technology

```html
<!DOCTYPE html>
<html lang="en">
<head>
<meta charset="utf-8">
<title>Brivolt Technologies – Business Card</title>
<link href="https://fonts.googleapis.com/css2?family=Saira+Semi+Condensed:wght@300;400;600&display=swap" rel="stylesheet">
<style>
  :root {
    --backdrop: #8e8e8e;
    --card-dark: #403f41;
    --card-light: #ffffff;
    --accent: #f7941d;
    --ink: #3a3a3a;
    --white: #ffffff;
    --grey-deep: #6f6f6f;
    --grey-pale: #f1f1f1;
  }
  * { margin: 0; padding: 0; box-sizing: border-box; }
  html, body {
    width: 1200px; height: 1200px; overflow: hidden;
    background: var(--backdrop);
    font-family: "Saira Semi Condensed", sans-serif;
  }
  .canvas { position: relative; width: 1200px; height: 1200px; }
  .card {
    position: absolute; left: 281px; width: 638px; height: 365px;
    border-radius: 22px; overflow: hidden;
  }
  .card--front { top: 195px; background: var(--card-dark); }
  .card--back { top: 639px; background: var(--card-light); }

  .brand {
    position: absolute; left: 0; right: 0; top: 150px;
    display: flex; align-items: center; justify-content: center; gap: 14px;
  }
  .brand__mark { width: 22px; height: 22px; background: var(--accent); }
  .brand__name {
    color: var(--white); font-weight: 600; font-size: 38px;
    letter-spacing: 2px; text-transform: uppercase; line-height: 1;
  }
  .card__band { position: absolute; left: 0; top: 0; }

  .person { position: absolute; left: 48px; top: 264px; }
  .person__name {
    color: var(--accent); font-weight: 600; font-size: 33px;
    line-height: 1; letter-spacing: 0.5px;
  }
  .person__role { color: var(--ink); font-weight: 400; font-size: 18px; margin-top: 6px; }

  .contact {
    position: absolute; right: 48px; top: 254px;
    list-style: none; text-align: right;
  }
  .contact__item {
    display: flex; justify-content: flex-end; align-items: center; gap: 10px;
    color: var(--ink); font-weight: 300; font-size: 16.5px; line-height: 22px;
  }
  .contact__icon { width: 12px; height: 12px; fill: var(--accent); flex: none; }
</style>
</head>
<body>
<main class="canvas">
  <section class="card card--front" aria-label="Card front">
    <div class="brand">
      <span class="brand__mark"></span>
      <span class="brand__name">Brivolt Technologies</span>
    </div>
    <svg class="card__band" width="638" height="365" viewBox="0 0 638 365" role="img" aria-label="Grey diagonal band with scattered tilted squares">
      <defs>
        <linearGradient id="front-band" x1="0" y1="0" x2="1" y2="0">
          <stop offset="0" stop-color="#8a8a8a"/>
          <stop offset="1" stop-color="#4a4a4c"/>
        </linearGradient>
      </defs>
      <polygon points="0,296 122,365 0,365" fill="url(#front-band)"/>
    </svg>
  </section>

  <section class="card card--back" aria-label="Card back">
    <svg class="card__band" width="638" height="365" viewBox="0 0 638 365" role="img" aria-label="Pattern of tilted grey squares fading from dark to light">
      <defs>
        <linearGradient id="back-pattern" x1="0" y1="0" x2="1" y2="0">
          <stop offset="0" stop-color="var(--grey-deep)"/>
          <stop offset="1" stop-color="var(--grey-pale)"/>
        </linearGradient>
      </defs>
      <polygon points="0,0 610,0 500,170 170,220 0,180" fill="url(#back-pattern)"/>
    </svg>

    <div class="person">
      <p class="person__name">DANIEL MARSH</p>
      <p class="person__role">Founder &amp; CEO</p>
    </div>

    <ul class="contact">
      <li class="contact__item">(555) 214-7730
        <svg class="contact__icon" viewBox="0 0 12 12" aria-hidden="true"><path d="M2.4 0.6 4.2 2.6 3.3 4.1C3.9 5.6 5.2 7.2 7 8.2L8.4 7.4 10.6 9 9.7 11C5.4 10.8 1 6.4 0.9 2Z"/></svg>
      </li>
      <li class="contact__item">daniel@brivolttechnologies.com
        <svg class="contact__icon" viewBox="0 0 12 12" aria-hidden="true"><path d="M0 2.5H12V10H0Z M0.8 3.2 6 7 11.2 3.2" stroke="#fff" stroke-width="0.9"/></svg>
      </li>
      <li class="contact__item">brivolttechnologies.com
        <svg class="contact__icon" viewBox="0 0 12 12" aria-hidden="true"><circle cx="6" cy="6" r="5.6"/><path d="M0.6 6H11.4M6 0.5C3.8 3.5 3.8 8.5 6 11.5M6 0.5C8.2 3.5 8.2 8.5 6 11.5" stroke="#fff" stroke-width="0.8" fill="none"/></svg>
      </li>
    </ul>
  </section>
</main>
</body>
</html>
```